Animal Horse & Bedding Company Needs a Website Coded & Designed

We need a website for a new animal bedding and feed company that is visually grabbing and vibrant. We would like to see a website that displays trust, quality and confidence. Needs to be responsive and mobile friendly for all browsers and coded for both Android & IOS. SEO is also important.

Joomla or Wordpress – must be both desktop and mobile friendly with fast page load speed. Need the ability to edit ourselves in Wordpress or Joomla.

Full details attached below with some layout and content ideas.

Coding

Coded - Design and coding required

Number of Pages Required

5+ page

Font styles to use
Sans Serif

Requirements
Must have
• Needs to be responsive and mobile friendly for all browsers and coded for both Android & IOS. SEO is also important.

Wordpress – must be both desktop and mobile friendly with fast page load speed. Need the ability to edit ourselves in Wordpress.

Logo Colours:
Dark Brown
CMYK: 50 / 70 / 80 / 70
Pantone: 4625C

Orange
CMYK: 0 / 50 / 100 / 0
Pantone: 144C
Nice to have
• Use picture of building attached and super impose logo on building.

```html
<!DOCTYPE html>
<html lang="en">
<head>
<meta charset="utf-8">
<title>Harvest Stall – Bedding &amp; Feed</title>
<link rel="stylesheet" href="https://fonts.googleapis.com/css2?family=Oswald:wght@300;400&family=Poppins:wght@400;500;600&display=swap">
<style>
:root{
  --brown:#3f2212;
  --orange:#f7941d;
  --white:#ffffff;
  --ink:#3a3a3a;
  --muted:#8a8a8a;
  --stage:#ffffff;
}
*{box-sizing:border-box;margin:0;padding:0}
html,body{width:1200px;height:2866px;overflow:hidden;background:var(--stage)}
body{font-family:"Poppins",sans-serif;color:var(--ink);position:relative}
.page{position:absolute;left:120px;top:56px;width:960px;height:2753px;background:var(--white);box-shadow:0 0 24px rgba(0,0,0,.12)}
.display{font-family:"Oswald",sans-serif;font-weight:300;text-transform:uppercase;letter-spacing:.5px}
.btn{position:absolute;background:var(--orange);color:var(--white);font-family:"Oswald",sans-serif;font-size:11px;letter-spacing:1.5px;text-transform:uppercase;display:flex;align-items:center;justify-content:center;border-radius:2px}
section{position:relative;overflow:hidden}

/* header */
.site-header{height:102px;background:var(--brown);color:var(--white)}
.brand{position:absolute;left:87px;top:14px;display:flex;align-items:center;gap:9px}
.brand-dot{width:26px;height:26px;border-radius:50%;background:var(--orange)}
.brand-name{font-family:"Oswald",sans-serif;font-weight:400;font-size:22px;letter-spacing:1px;text-transform:uppercase;line-height:1}
.search{position:absolute;left:557px;top:26px;width:214px;height:24px;background:var(--white);border-radius:2px;font-size:9px;color:#bbb;padding:6px 10px}
.search svg{position:absolute;right:8px;top:7px}
.icon-user{position:absolute;left:808px;top:30px}
.icon-cart{position:absolute;left:848px;top:29px}
.header-rule{position:absolute;left:87px;top:72px;width:777px;height:1px;background:rgba(255,255,255,.35)}
.main-nav{position:absolute;top:80px;left:0;width:100%;font-size:12px}
.main-nav span{position:absolute;white-space:nowrap}

/* hero */
.hero{height:476px}
.hero-photo{position:absolute;inset:0;background:
  radial-gradient(ellipse 220px 300px at 330px 250px,#e9ddc6 0%,#c9b08a 45%,rgba(150,100,40,0) 75%),
  radial-gradient(ellipse 300px 220px at 820px 120px,#e8a34a 0%,rgba(200,120,40,0) 70%),
  linear-gradient(100deg,#8a5a1e 0%,#b0782c 25%,#5a3a18 55%,#20271c 72%,#6b4a20 100%)}
.hero-copy{position:absolute;left:488px;color:var(--white);white-space:nowrap}
.hero-kicker{top:110px;font-size:26px;line-height:1}
.hero-title{top:150px;font-size:62px;line-height:1;font-weight:400}
.hero-sub{top:242px;font-size:34px;line-height:1;letter-spacing:1.5px}
.hero .btn{left:488px;top:300px;width:107px;height:26px}

/* about */
.about{height:404px}
.about-mark{position:absolute;left:122px;top:61px;width:206px;height:275px;display:flex;flex-direction:column;align-items:center;justify-content:center;gap:14px}
.about-mark .dot{width:120px;height:120px;border-radius:50%;background:var(--brown)}
.about-mark .name{font-family:"Oswald",sans-serif;font-size:22px;color:var(--brown);text-transform:uppercase;letter-spacing:1px}
.section-title{position:absolute;color:var(--brown);font-size:34px;line-height:1}
.title-rule{position:absolute;height:3px;width:62px;background:var(--brown)}
.about .section-title{left:459px;top:84px}
.about .title-rule{left:459px;top:128px}
.about-text{position:absolute;left:459px;top:145px;width:378px;font-size:10.5px;line-height:16.6px;color:#333}
.about .btn{left:459px;top:304px;width:106px;height:26px}

/* benefits */
.benefit{height:313px}
.benefit-photo{position:absolute;inset:0}
.bedding-photo{background:linear-gradient(180deg,#5d5a4a 0%,#6d6e4c 35%,#4f7a2a 70%,#5f8f2c 100%)}
.bedding-photo::after{content:"";position:absolute;left:560px;top:20px;width:330px;height:270px;background:radial-gradient(ellipse at center,rgba(150,70,30,.85) 0%,rgba(150,70,30,0) 70%)}
.feed-photo{background:linear-gradient(180deg,#7a6a2e 0%,#667a30 40%,#4b6e22 100%)}
.feed-photo::after{content:"";position:absolute;left:40px;top:40px;width:480px;height:240px;background:radial-gradient(ellipse at center,rgba(90,40,25,.85) 0%,rgba(90,40,25,0) 70%)}
.benefit-box{position:absolute;top:43px;width:385px;height:229px;background:rgba(40,30,20,.72);border:1px solid var(--orange);color:var(--white);padding:22px 0 0 38px}
.benefit-box h2{font-size:34px;line-height:1;font-weight:300}
.benefit-list{display:flex;gap:18px;margin-top:12px;font-size:8.5px;line-height:12px;letter-spacing:.4px}
.benefit-list ul{list-style:none;width:125px}
.benefit-list ul+ul{width:185px}
.benefit-box .btn{left:38px;top:178px;width:106px;height:26px}
.bedding .benefit-box{left:43px}
.feed .benefit-box{left:531px;top:41px}

/* products */
.products{height:366px}
.products .section-title{left:78px;top:60px}
.products .title-rule{left:78px;top:104px}
.product-card{position:absolute;top:140px;width:253px;height:134px;background:var(--white);box-shadow:0 1px 6px rgba(0,0,0,.12)}
.product-photo{position:absolute;left:15px;top:19px;width:100px;height:96px}
.product-card h3{position:absolute;left:140px;top:38px;font-size:10px;font-weight:600;line-height:12px;color:#333}
.product-card .btn{left:140px;top:84px;width:80px;height:22px;font-size:8px}
.slider-arrow{position:absolute;top:196px;font-size:20px;color:#555;letter-spacing:-3px}

/* testimonials */
.testimonials{height:496px}
.testimonials .section-title{left:0;width:100%;text-align:center;top:56px;font-size:38px}
.testimonials .title-rule{left:449px;top:102px}
.quote-card{position:absolute;top:142px;width:202px;height:224px;background:var(--white);box-shadow:0 1px 7px rgba(0,0,0,.12);text-align:center}
.avatar{width:34px;height:34px;border-radius:50%;background:#b7bcc4;margin:26px auto 0}
.quote-card h4{font-size:11px;font-weight:600;color:var(--brown);margin-top:8px}
.stars{display:flex;justify-content:center;margin-top:4px}
.quote-card p{font-size:8.5px;line-height:14.5px;color:var(--muted);width:165px;margin:12px auto 0}
.round-arrow{position:absolute;top:242px;width:22px;height:22px}

/* newsletter */
.newsletter{position:absolute;left:110px;top:2422px;width:740px;height:72px;background:var(--orange);z-index:2}
.newsletter h3{position:absolute;left:27px;top:26px;font-size:17px;line-height:1;color:var(--brown);font-weight:400}
.newsletter .email{position:absolute;left:253px;top:20px;width:328px;height:30px;background:var(--white);font-size:10px;color:#aaa;padding:9px 13px}
.newsletter .subscribe{position:absolute;left:592px;top:20px;width:131px;height:30px;background:var(--brown);color:var(--white);font-size:14px;display:flex;align-items:center;justify-content:center}

/* footer */
.site-footer{position:absolute;left:0;top:2471px;width:960px;height:282px;background:var(--brown);color:var(--white)}
.footer-brand{position:absolute;left:130px;top:70px;display:flex;align-items:center;gap:8px}
.footer-brand .brand-dot{width:20px;height:20px}
.footer-brand .brand-name{font-size:19px}
.footer-about{position:absolute;left:130px;top:138px;width:180px;font-size:9.5px;line-height:15px;letter-spacing:.6px}
.footer-col{position:absolute;top:68px;font-size:9.5px}
.footer-col h5{font-size:14px;font-weight:500;padding-bottom:4px;border-bottom:1px solid var(--white);display:inline-block;margin-bottom:14px}
.footer-col li{list-style:none}
.contact-col{left:369px}
.contact-col li{margin-bottom:20px;font-size:10px;letter-spacing:.5px}
.links-col{left:540px}
.links-col li{line-height:17px;font-weight:500}
.connect-col{left:710px}
.connect-col .tag{font-size:6.5px;margin:-8px 0 10px}
.connect-col li{display:flex;align-items:center;gap:12px;margin-bottom:11px;font-size:9.5px}
.connect-col li i{width:10px;height:10px;background:var(--white);border-radius:2px;display:block}
.footer-rule{position:absolute;left:110px;top:252px;width:740px;height:1px;background:rgba(255,255,255,.45)}
.copyright{position:absolute;left:0;width:100%;top:259px;text-align:center;font-size:9.5px}
</style>
</head>
<body>
<div class="page">

  <header class="site-header">
    <div class="brand"><span class="brand-dot"></span><span class="brand-name">Harvest Stall</span></div>
    <div class="search">Search
      <svg width="9" height="9" viewBox="0 0 10 10"><circle cx="4" cy="4" r="3" fill="none" stroke="#f7941d" stroke-width="1.5"/><line x1="6.2" y1="6.2" x2="9" y2="9" stroke="#f7941d" stroke-width="1.5"/></svg>
    </div>
    <svg class="icon-user" width="14" height="14" viewBox="0 0 14 14"><circle cx="7" cy="4" r="3.2" fill="#fff"/><path d="M1 14c0-4 3-6 6-6s6 2 6 6z" fill="#fff"/></svg>
    <svg class="icon-cart" width="19" height="16" viewBox="0 0 19 16"><path d="M0 1h3l2.5 9h10l2.5-7H5" fill="none" stroke="#fff" stroke-width="1.8"/><path d="M5 3h13l-2.5 7h-10z" fill="#fff"/><circle cx="7" cy="14" r="1.6" fill="#fff"/><circle cx="14.5" cy="14" r="1.6" fill="#fff"/></svg>
    <div class="header-rule"></div>
    <nav class="main-nav">
      <span style="left:209px">Home</span><span style="left:290px">About</span><span style="left:371px">Feed</span><span style="left:446px">Bedding</span><span style="left:542px">Contact Us</span><span style="left:653px">Requets Quote</span>
    </nav>
  </header>

  <section class="hero">
    <div class="hero-photo" role="img" aria-label="White horse in a halter against warm autumn foliage"></div>
    <div class="hero-copy display hero-kicker">Wellcome</div>
    <div class="hero-copy display hero-title">Harvest Stall</div>
    <div class="hero-copy display hero-sub">Bedding &amp; Feed</div>
    <div class="btn">Shop Now</div>
  </section>

  <section class="about">
    <div class="about-mark"><span class="dot"></span><span class="name">Harvest Stall</span></div>
    <h2 class="section-title display">About Us</h2>
    <div class="title-rule"></div>
    <p class="about-text">Looking for the best bedding and feed for your horse, livestock or household pet look no further. We use premium locally sourced straw and hay in all of our products and are committed in providing quality products and service.<br>Your animal deserves the very best in health and comfort to keep them healthy, strong and happy. Our products are designed for horses, livestock (goats, cattle and sheep), small caged animals (rabbits, guinea pigs and more).</p>
    <div class="btn">Learn More</div>
  </section>

  <section class="benefit bedding">
    <div class="benefit-photo bedding-photo" role="img" aria-label="Chestnut foal holding a feed bucket on a green paddock"></div>
    <div class="benefit-box">
      <h2 class="display">Bedding Benefit</h2>
      <div class="benefit-list">
        <ul><li>• 100% Natural Chopped<br>&nbsp;&nbsp;Straw</li><li>• Low Dust</li><li>• Chemical &amp; Additive Free</li><li>• Clean &amp; Highly Absorbent</li><li>• Cheaper than Wood<br>&nbsp;&nbsp;Shavings</li></ul>
        <ul><li>• Economic – less used and less wasted</li><li>• Environmentally Friendly – Recyclable<br>&nbsp;&nbsp;&amp; Compostable</li></ul>
      </div>
      <div class="btn">Shop Now</div>
    </div>
  </section>

  <section class="products">
    <h2 class="section-title display">Our Products</h2>
    <div class="title-rule"></div>
    <span class="slider-arrow" style="left:30px">&lt;&lt;</span>
    <article class="product-card" style="left:78px">
      <div class="product-photo" role="img" aria-label="Bay horse grazing" style="background:linear-gradient(135deg,#6f8a3a,#8a4a22)"></div>
      <h3>Best Bedding<br>For Your Horse</h3>
      <div class="btn">Requets Quote</div>
    </article>
    <article class="product-card" style="left:351px">
      <div class="product-photo" role="img" aria-label="Woolly sheep in a field" style="background:linear-gradient(135deg,#d9c9a8,#9a7a50)"></div>
      <h3>Best Bedding<br>For Your Horse</h3>
      <div class="btn">Requets Quote</div>
    </article>
    <article class="product-card" style="left:627px">
      <div class="product-photo" role="img" aria-label="White rabbit on grass" style="background:linear-gradient(135deg,#4e6a2a,#e6e6e0)"></div>
      <h3>Best Feed For<br>Your Horse</h3>
      <div class="btn">Requets Quote</div>
    </article>
    <span class="slider-arrow" style="left:906px">&gt;&gt;</span>
  </section>

  <section class="benefit feed">
    <div class="benefit-photo feed-photo" role="img" aria-label="Brown and white dairy cows grazing in a pasture"></div>
    <div class="benefit-box">
      <h2 class="display">Feed Benefit</h2>
      <div class="benefit-list">
        <ul style="width:150px"><li>• 100% Natural</li><li>• Chemical &amp; Additive Free</li><li>• Available in Pellets or Cubes</li><li>• High Protein Content</li><li>• Eliminate Waste in Feeding</li><li>• Clean – Eliminates Dust From<br>&nbsp;&nbsp;Feeding Baled Hay</li></ul>
        <ul style="width:120px"><li>• Cost Effective</li><li>• Convenient</li><li>• Less wasted feed</li></ul>
      </div>
      <div class="btn">Shop Now</div>
    </div>
  </section>

  <section class="testimonials">
    <h2 class="section-title display">Testimonial</h2>
    <div class="title-rule"></div>
    <svg class="round-arrow" style="left:58px" viewBox="0 0 22 22"><circle cx="11" cy="11" r="11" fill="#333"/><path d="M15 11H7m3-4-4 4 4 4" fill="none" stroke="#fff" stroke-width="2"/></svg>
    <article class="quote-card" style="left:136px">
      <div class="avatar" role="img" aria-label="Customer portrait"></div>
      <h4>Daniel Marsh</h4>
      <div class="stars"><svg width="60" height="9" viewBox="0 0 60 9"><g fill="#f7941d"><polygon points="4.5,0 5.6,3.3 9,3.3 6.2,5.3 7.3,8.6 4.5,6.6 1.7,8.6 2.8,5.3 0,3.3 3.4,3.3"/><polygon transform="translate(12.5)" points="4.5,0 5.6,3.3 9,3.3 6.2,5.3 7.3,8.6 4.5,6.6 1.7,8.6 2.8,5.3 0,3.3 3.4,3.3"/><polygon transform="translate(25)" points="4.5,0 5.6,3.3 9,3.3 6.2,5.3 7.3,8.6 4.5,6.6 1.7,8.6 2.8,5.3 0,3.3 3.4,3.3"/><polygon transform="translate(37.5)" points="4.5,0 5.6,3.3 9,3.3 6.2,5.3 7.3,8.6 4.5,6.6 1.7,8.6 2.8,5.3 0,3.3 3.4,3.3"/><polygon transform="translate(50)" points="4.5,0 5.6,3.3 9,3.3 6.2,5.3 7.3,8.6 4.5,6.6 1.7,8.6 2.8,5.3 0,3.3 3.4,3.3"/></g></svg></div>
      <p>Lorem ipsum dolor sit amet, consectetur adipiscing elit ut aliquam, purus sit amet luctus venenatis, lectus magna purus sit amet luctus venenatis.</p>
    </article>
    <article class="quote-card" style="left:379px">
      <div class="avatar" role="img" aria-label="Customer portrait"></div>
      <h4>Daniel Marsh</h4>
      <div class="stars"><svg width="60" height="9" viewBox="0 0 60 9"><g fill="#f7941d"><polygon points="4.5,0 5.6,3.3 9,3.3 6.2,5.3 7.3,8.6 4.5,6.6 1.7,8.6 2.8,5.3 0,3.3 3.4,3.3"/><polygon transform="translate(12.5)" points="4.5,0 5.6,3.3 9,3.3 6.2,5.3 7.3,8.6 4.5,6.6 1.7,8.6 2.8,5.3 0,3.3 3.4,3.3"/><polygon transform="translate(25)" points="4.5,0 5.6,3.3 9,3.3 6.2,5.3 7.3,8.6 4.5,6.6 1.7,8.6 2.8,5.3 0,3.3 3.4,3.3"/><polygon transform="translate(37.5)" points="4.5,0 5.6,3.3 9,3.3 6.2,5.3 7.3,8.6 4.5,6.6 1.7,8.6 2.8,5.3 0,3.3 3.4,3.3"/><polygon transform="translate(50)" points="4.5,0 5.6,3.3 9,3.3 6.2,5.3 7.3,8.6 4.5,6.6 1.7,8.6 2.8,5.3 0,3.3 3.4,3.3"/></g></svg></div>
      <p>Lorem ipsum dolor sit amet, consectetur adipiscing elit ut aliquam, purus sit amet luctus venenatis, lectus magna purus sit amet luctus venenatis.</p>
    </article>
    <article class="quote-card" style="left:623px">
      <div class="avatar" role="img" aria-label="Customer portrait"></div>
      <h4>Daniel Marsh</h4>
      <div class="stars"><svg width="60" height="9" viewBox="0 0 60 9"><g fill="#f7941d"><polygon points="4.5,0 5.6,3.3 9,3.3 6.2,5.3 7.3,8.6 4.5,6.6 1.7,8.6 2.8,5.3 0,3.3 3.4,3.3"/><polygon transform="translate(12.5)" points="4.5,0 5.6,3.3 9,3.3 6.2,5.3 7.3,8.6 4.5,6.6 1.7,8.6 2.8,5.3 0,3.3 3.4,3.3"/><polygon transform="translate(25)" points="4.5,0 5.6,3.3 9,3.3 6.2,5.3 7.3,8.6 4.5,6.6 1.7,8.6 2.8,5.3 0,3.3 3.4,3.3"/><polygon transform="translate(37.5)" points="4.5,0 5.6,3.3 9,3.3 6.2,5.3 7.3,8.6 4.5,6.6 1.7,8.6 2.8,5.3 0,3.3 3.4,3.3"/><polygon transform="translate(50)" points="4.5,0 5.6,3.3 9,3.3 6.2,5.3 7.3,8.6 4.5,6.6 1.7,8.6 2.8,5.3 0,3.3 3.4,3.3"/></g></svg></div>
      <p>Lorem ipsum dolor sit amet, consectetur adipiscing elit ut aliquam, purus sit amet luctus venenatis, lectus magna purus sit amet luctus venenatis.</p>
    </article>
    <svg class="round-arrow" style="left:869px" viewBox="0 0 22 22"><circle cx="11" cy="11" r="11" fill="#333"/><path d="M7 11h8m-3-4 4 4-4 4" fill="none" stroke="#fff" stroke-width="2"/></svg>
  </section>

  <div class="newsletter">
    <h3 class="display">Subscribe for Newsletter</h3>
    <div class="email">Your Email Address</div>
    <div class="subscribe display">Subscribe</div>
  </div>

  <footer class="site-footer">
    <div class="footer-brand"><span class="brand-dot"></span><span class="brand-name">Harvest Stall</span></div>
    <p class="footer-about">Harvest Stall offers supply and delivery of fresh bedding as well as removal of waste bedding.</p>
    <div class="footer-col contact-col">
      <h5>Get in touch</h5>
      <ul><li>0800-410-2201</li><li>022-3104-5567</li><li>0800-410-7734</li></ul>
    </div>
    <div class="footer-col links-col">
      <h5>Useful Links</h5>
      <ul><li>Home</li><li>About</li><li>Feed</li><li>Bedding</li><li>Contact Us</li><li>Request Quote</li></ul>
    </div>
    <div class="footer-col connect-col">
      <h5>Connect</h5>
      <p class="tag">Part of the Meadow Crest family</p>
      <ul><li><i></i>Photos</li><li><i></i>Community</li><li><i></i>Updates</li><li><i></i>Videos</li></ul>
    </div>
    <div class="footer-rule"></div>
    <p class="copyright">© Copyright 2020 Harvest Stall. All Rights Reserved.</p>
  </footer>

</div>
</body>
</html>
```